Homemaking training schools needs a Business Card design

Designer, Hello!

No special requirements, good-looking enough.
--------------------------------------------------------------------------

Name: Marcus Dole
Chairman
Tel: 0574-71948263
Mobile: 13857420916
Email: kelvora@mailnest.example
Web: www.prt2019.example
Add: No.258, LanpingJie, BeiyuanQu, Ningbo, Zhejiang

LOGO
Ningbo PRT Homemaking Training School

Target Market(s)

pregnant women, mothers, infants, the elderly and families, including cleaning, cooking, nursing training.

Industry/Entity Type

Business

Contact Information for Business Card

Name: Marcus Dole
Chairman
Tel: 0574-71948263
Mobile: 13857420916
Email: kelvora@mailnest.example
Web: www.prt2019.example

LOGO

Font styles to use
Serif
Sans Serif
Decorative

Requirements
Nice to have
• Feels: clean, specifications, safety, comfort, warmth and happiness.

```html
<!DOCTYPE html>
<html lang="en">
<head>
<meta charset="utf-8">
<title>PuRenTang Business Card</title>
<link rel="stylesheet" href="https://fonts.googleapis.com/css2?family=Raleway:wght@400;500&display=swap">
<style>
  :root {
    --page: #e8e6e3;
    --ink: #231f20;
    --blue: #0a6fbd;
    --blue-deep: #0a4f86;
    --pink: #e5008a;
    --white: #ffffff;
  }
  * { margin: 0; padding: 0; box-sizing: border-box; }
  html, body { width: 1200px; height: 900px; overflow: hidden; }
  body {
    background: var(--page);
    font-family: "Raleway", sans-serif;
    position: relative;
  }
  .card {
    position: absolute;
    left: 240px;
    width: 720px;
    height: 400px;
    overflow: hidden;
    box-shadow: 0 6px 18px rgba(0,0,0,0.18);
    background: var(--ink);
  }
  .card-front { top: 30px; }
  .card-back { top: 470px; }
  .card-shapes { position: absolute; inset: 0; width: 100%; height: 100%; }

  .company-name {
    position: absolute;
    color: var(--white);
    font-weight: 500;
    line-height: 1;
    white-space: nowrap;
  }
  .card-front .company-name {
    left: 50%; top: 180px;
    transform: translateX(-50%);
    font-size: 42px;
  }
  .card-back .company-name {
    left: 72px; top: 312px;
    font-size: 36px;
  }

  .holder { position: absolute; right: 360px; top: 82px; text-align: right; color: var(--white); }
  .holder-name { font-size: 31px; font-weight: 500; letter-spacing: 1px; text-transform: uppercase; }
  .holder-role { font-size: 25px; font-weight: 400; }
  .divider { position: absolute; left: 386px; top: 62px; width: 2px; height: 110px; background: var(--white); }

  .contact-list { position: absolute; left: 412px; top: 62px; list-style: none; color: var(--white); }
  .contact-list li { display: flex; align-items: center; gap: 10px; font-size: 20px; height: 28px; white-space: nowrap; }
  .contact-list svg { width: 20px; height: 20px; flex: none; }

  .address { position: absolute; left: 424px; top: 304px; color: var(--white); font-size: 20px; line-height: 1.45; }
</style>
</head>
<body>

  <section class="card card-front">
    <svg class="card-shapes" viewBox="0 0 720 400" aria-hidden="true">
      <circle cx="18" cy="18" r="48" fill="var(--pink)"/>
      <path d="M0 70 Q110 120 90 230 Q80 290 0 360 Z" fill="var(--blue)"/>
      <path d="M0 160 Q55 180 45 230 Q40 260 0 270 Z" fill="var(--pink)"/>
      <circle cx="705" cy="18" r="48" fill="var(--pink)"/>
      <path d="M720 70 Q630 110 630 190 Q630 270 720 320 Z" fill="var(--blue)"/>
      <path d="M720 150 Q670 160 672 200 Q675 235 720 245 Z" fill="var(--pink)"/>
    </svg>
    <div class="company-name">PuRenTang</div>
  </section>

  <section class="card card-back">
    <svg class="card-shapes" viewBox="0 0 720 400" aria-hidden="true">
      <rect width="720" height="400" fill="var(--blue)"/>
      <path d="M0 215 Q150 175 330 215 Q520 262 720 230 L720 400 L0 400 Z" fill="var(--blue-deep)"/>
      <path d="M0 240 Q150 200 330 235 Q520 275 720 252 L720 400 L0 400 Z" fill="var(--ink)"/>
    </svg>

    <div class="holder">
      <div class="holder-name">Marcus Dole</div>
      <div class="holder-role">Chairman</div>
    </div>
    <div class="divider"></div>

    <ul class="contact-list">
      <li>
        <svg viewBox="0 0 20 20"><circle cx="10" cy="10" r="8.5" fill="none" stroke="#fff" stroke-width="1.4"/><path d="M7 5.5l2 2-1 1.2c.6 1.3 1.6 2.3 2.9 2.9l1.2-1 2 2-1.2 1.4C9.5 14 6 10.5 5.6 6.7z" fill="#fff"/></svg>
        <span>0574-71948263</span>
      </li>
      <li>
        <svg viewBox="0 0 20 20"><circle cx="10" cy="10" r="8.5" fill="none" stroke="#fff" stroke-width="1.4"/><rect x="7" y="5" width="6" height="10" rx="1" fill="none" stroke="#fff" stroke-width="1.4"/></svg>
        <span>13857420916</span>
      </li>
      <li>
        <svg viewBox="0 0 20 20"><rect x="2" y="5" width="16" height="11" fill="none" stroke="#fff" stroke-width="1.4"/><path d="M2 5l8 6 8-6" fill="none" stroke="#fff" stroke-width="1.4"/></svg>
        <span>kelvora@mailnest.example</span>
      </li>
      <li>
        <svg viewBox="0 0 20 20"><circle cx="10" cy="10" r="8.5" fill="none" stroke="#fff" stroke-width="1.4"/><path d="M1.5 10h17M10 1.5c-3 3-3 14 0 17M10 1.5c3 3 3 14 0 17" fill="none" stroke="#fff" stroke-width="1.2"/></svg>
        <span>www.prt2019.example</span>
      </li>
    </ul>

    <div class="company-name">PuRenTang</div>

    <p class="address">No.258, LanpingJie<br>BeiyuanQu, Ningbo, Zhejiang</p>
  </section>

</body>
</html>
```